RPT Event Lead Generation eFlyer

We need a brochure that highlights our Experiential Marketing and Event Management services. Using our corporate branding, images and icons, great an engaging and dynamic sales tool for our company designed to find qualified new business leads.

I would like the eFlyer in PDF format to send to clients via email, but would also like a working file (.doc) so that I can change the copy if needed.

Note: This is the first in a series of flyers. I would also eventually like to have printed versions, but for now I'm only doing electronic. My company offers 3 services: 1. Business Development; 2. Marketing Communications (this is the flyer you are working on); 3. Keynotes, i.e. motivational speaking. I will be producing a flyer for each of those services. The branding will be similar but the messaging will have a focus on the specific service.
Updates

Project Deadline Extended
Reason: I'm using this first experience with Pixel Harbor as a test. I'm looking for an affordable solution for ongoing design work. I would like to see more options coming in so that I can not only choose a great flyer, but can also choose a long term designer.

Target Market(s)

Marketing and Advertising Agencies, Production Companies

Industry/Entity Type

Marketing

Colors
e667a6
5c5c5c

Requirements
Must have
• Would like it to be clear, simple and inspiring. I want them to call me to discuss a project.
Nice to have
• Can convert copy to info graphs, I would like it to be visual and easy for someone to scan and get the information quickly.
Should not have
• I don't want it to be copy heavy.

```html
<!DOCTYPE html>
<html lang="en">
<head>
<meta charset="utf-8">
<title>RPT Partners – Experiential Marketing &amp; Event Management</title>
<link href="https://fonts.googleapis.com/css2?family=Raleway:wght@400;500;600;700;800&display=swap" rel="stylesheet">
<style>
:root{
  --magenta:#d41f63;
  --charcoal:#404040;
  --ink:#4a4a4a;
  --grey-text:#5c5c5c;
  --panel:#ebebeb;
  --stage:#a6a6a6;
  --white:#ffffff;
}
*{box-sizing:border-box;margin:0;padding:0}
html,body{width:1200px;height:1200px;overflow:hidden}
body{background:var(--stage);font-family:'Raleway',sans-serif;color:var(--ink);position:relative;font-variant-numeric:lining-nums}
.flyer{position:absolute;left:189px;top:20px;width:821px;height:1160px;background:var(--white);overflow:hidden}

/* hero */
.hero{position:absolute;left:0;top:0;width:821px;height:415px}
.hero-art{position:absolute;inset:0;background:linear-gradient(90deg,#111 0%,#3a3a3a 45%,#cfcfcf 62%,#f2f2f2 100%)}
.hero-panel{position:absolute;left:0;top:135px;width:560px;height:280px;background:linear-gradient(90deg,#c8c8c8,#d8d8d8);clip-path:polygon(0 0,100% 0,82% 100%,0 100%)}
.brand{position:absolute;left:560px;top:58px;display:flex;align-items:center;gap:12px}
.brand-mark{width:26px;height:26px;background:var(--magenta)}
.brand-name{font-weight:700;font-size:26px;line-height:30px;color:var(--charcoal)}
.headline{position:absolute;left:34px;top:178px;font-weight:800;font-size:35px;line-height:42px;color:var(--charcoal);letter-spacing:-.5px;text-transform:uppercase}
.intro{position:absolute;left:34px;top:264px;width:420px;font-weight:500;font-size:26px;line-height:33px;color:var(--grey-text);letter-spacing:-.4px}
.intro strong{font-weight:800;color:var(--charcoal)}

/* pink band */
.callout{position:absolute;left:0;top:415px;width:821px;height:84px;background:var(--magenta);color:var(--white);font-weight:700;font-size:18.5px;line-height:25px;padding:19px 30px 0 35px}

/* services */
.services{position:absolute;left:0;top:499px;width:821px;height:223px;display:grid;grid-template-columns:271px 271px 279px;padding:13px 0 0 33px}
.svc-col{list-style:none;position:relative}
.svc-col+.svc-col::before{content:"";position:absolute;left:-26px;top:6px;width:2px;height:190px;background:linear-gradient(#fff,#ddd,#fff)}
.svc-col li{display:flex;gap:8px;font-size:15px;line-height:21px;color:var(--grey-text);margin-bottom:12px;font-weight:500}
.svc-col li svg{flex:none;width:20px;height:20px;margin-top:1px}
.svc-col.first li{margin-bottom:10px}

/* strengths */
.strengths{position:absolute;left:0;top:722px;width:821px;height:204px;background:var(--panel)}
.strengths-intro{position:absolute;left:33px;top:13px;width:760px;font-weight:700;font-size:15.5px;line-height:21px;color:var(--charcoal)}
.strength-grid{position:absolute;left:34px;top:73px;display:grid;grid-template-columns:282px 282px 220px;row-gap:26px}
.strength{display:flex;align-items:center;gap:12px}
.strength-icon{width:46px;height:46px;border-radius:50%;background:var(--magenta);display:flex;align-items:center;justify-content:center}
.strength-icon svg{width:26px;height:26px}
.strength-label{font-weight:700;font-size:21px;line-height:25px;color:var(--charcoal)}
.strength-rule{position:absolute;top:80px;width:2px;height:110px;background:linear-gradient(#ebebeb,#cfcfcf,#ebebeb)}

/* contact */
.team{position:absolute;left:203px;top:976px;width:600px;font-weight:700;font-size:15.5px;line-height:20px;color:var(--charcoal);text-transform:uppercase}
.contact-bar{position:absolute;left:0;top:1030px;width:821px;height:130px;background:var(--charcoal)}
.contact-tab{position:absolute;left:270px;top:0;width:438px;height:30px;background:var(--white);clip-path:polygon(0 0,100% 0,94% 100%,6% 100%);text-align:center;font-weight:700;font-size:16px;line-height:28px;color:var(--charcoal)}
.contact-name{position:absolute;left:203px;top:48px;display:flex;align-items:center;gap:6px;color:var(--white);font-size:23px;white-space:nowrap}
.contact-name b{font-weight:800}
.contact-name .title{font-weight:400}
.contact-name .phone{font-weight:800;margin-left:8px}
.contact-links{position:absolute;left:213px;top:86px;display:flex;align-items:center;gap:6px;color:var(--white);font-size:16.5px;font-weight:400;white-space:nowrap}
.contact-links .gap{width:14px}
.ico{width:22px;height:22px;flex:none}
.portrait{position:absolute;left:35px;top:947px;width:153px;height:181px;border-radius:16px;background:linear-gradient(160deg,#8b9a86,#d8c3a8 55%,#b8a690)}
</style>
</head>
<body>
<main class="flyer">
  <section class="hero">
    <div class="hero-art" role="img" aria-label="Tangled black scribbled lines leading to a rope with a businessman balancing on a tightrope"></div>
    <div class="hero-panel"></div>
    <div class="brand">
      <span class="brand-mark"></span>
      <span class="brand-name">RPT Partners</span>
    </div>
    <h1 class="headline">Experiential Marketing<br>&amp; Event Management</h1>
    <p class="intro">We offer agencies white label solutions. Need to fill a gap in a hurry with no time to hire?<br><strong>We can help!</strong></p>
  </section>

  <p class="callout">Our team plugs in and ramps up, to quickly deliver critical solutions that make a big impact on your business!&nbsp; Our services include:</p>

  <section class="services">
    <ul class="svc-col first">
      <li><svg viewBox="0 0 20 20"><circle cx="10" cy="9" r="5" fill="none" stroke="#d41f63" stroke-width="1.6"/><rect x="8" y="14" width="4" height="4" fill="#d41f63"/></svg>Ideation &amp; Concept<br>Development</li>
      <li><svg viewBox="0 0 20 20"><circle cx="10" cy="10" r="6" fill="#d41f63"/><circle cx="10" cy="10" r="2" fill="#fff"/></svg>Strategic Planning</li>
      <li><svg viewBox="0 0 20 20"><rect x="2" y="3" width="13" height="12" fill="none" stroke="#d41f63" stroke-width="1.6"/><circle cx="13" cy="13" r="3" fill="none" stroke="#d41f63" stroke-width="1.6"/><path d="M15 15l3 3" stroke="#d41f63" stroke-width="1.8"/></svg>Research &amp; Feasibility</li>
      <li><svg viewBox="0 0 20 20"><rect x="2" y="3" width="16" height="15" fill="none" stroke="#d41f63" stroke-width="1.6"/><path d="M2 7h16M7 7v11M12 7v11M2 12h16" stroke="#d41f63" stroke-width="1.2"/></svg>Event Creation &amp; Logistics</li>
      <li><svg viewBox="0 0 20 20"><path d="M10 2a5 5 0 0 1 5 5c0 4-5 8-5 8s-5-4-5-8a5 5 0 0 1 5-5z" fill="none" stroke="#d41f63" stroke-width="1.6"/><path d="M2 18h16" stroke="#d41f63" stroke-width="1.6"/></svg>Venue, Permit and<br>Supplier Negotiations</li>
    </ul>
    <ul class="svc-col">
      <li><svg viewBox="0 0 20 20"><circle cx="8" cy="6" r="4" fill="#d41f63"/><path d="M1 18c0-5 3-7 7-7s5 2 5 2v5z" fill="#d41f63"/><circle cx="15" cy="14" r="4" fill="#d41f63" stroke="#fff"/></svg>Registration Management</li>
      <li><svg viewBox="0 0 20 20"><path d="M3 14a7 7 0 0 1 14 0z" fill="#d41f63"/><rect x="1" y="15" width="18" height="2" fill="#d41f63"/></svg>Hospitality</li>
      <li><svg viewBox="0 0 20 20"><path d="M13 4h5l-1 14h-3z" fill="#d41f63"/><path d="M2 11h9M2 14h9M2 17h9" stroke="#d41f63" stroke-width="1.6"/></svg>Food &amp; Beverage</li>
      <li><svg viewBox="0 0 20 20"><path d="M3 3l14 14M17 3L3 17" stroke="#d41f63" stroke-width="2"/></svg>Design &amp; Décor</li>
      <li><svg viewBox="0 0 20 20"><circle cx="6" cy="13" r="4" fill="none" stroke="#d41f63" stroke-width="2"/><circle cx="14" cy="13" r="4" fill="none" stroke="#d41f63" stroke-width="2"/><circle cx="10" cy="5" r="3.5" fill="none" stroke="#d41f63" stroke-width="2"/></svg>Full Production Services</li>
      <li><svg viewBox="0 0 20 20"><rect x="2" y="5" width="16" height="12" fill="#d41f63"/><circle cx="10" cy="11" r="3.5" fill="#fff"/></svg>A/V, Lighting &amp; Sound</li>
    </ul>
    <ul class="svc-col">
      <li><svg viewBox="0 0 20 20"><circle cx="10" cy="10" r="4.5" fill="#d41f63"/><path d="M10 1v3M10 16v3M1 10h3M16 10h3M4 4l2 2M14 14l2 2M16 4l-2 2M4 16l2-2" stroke="#d41f63" stroke-width="1.5"/></svg>Creative Services</li>
      <li><svg viewBox="0 0 20 20"><rect x="3" y="4" width="14" height="10" fill="none" stroke="#d41f63" stroke-width="1.6"/><path d="M1 17h18" stroke="#d41f63" stroke-width="2"/></svg>Technology Management</li>
      <li><svg viewBox="0 0 20 20"><circle cx="10" cy="10" r="7" fill="none" stroke="#d41f63" stroke-width="1.8"/><path d="M3 13l14-7" stroke="#d41f63" stroke-width="2"/></svg>Travel Logistics</li>
      <li><svg viewBox="0 0 20 20"><circle cx="6" cy="5" r="3" fill="#d41f63"/><path d="M2 18v-7h8l3 3h5v4z" fill="#d41f63"/></svg>Speaker Management</li>
      <li><svg viewBox="0 0 20 20"><circle cx="10" cy="5" r="3" fill="#d41f63"/><path d="M6 15l4-6 4 6z" fill="#d41f63"/><path d="M2 17h16" stroke="#d41f63" stroke-width="1.6"/></svg>Delegate Management</li>
      <li><svg viewBox="0 0 20 20"><rect x="3" y="2" width="14" height="9" fill="none" stroke="#d41f63" stroke-width="1.6"/><circle cx="6" cy="14" r="2.5" fill="#d41f63"/><path d="M3 19v-3h6v3" fill="#d41f63"/></svg>On-site Management</li>
    </ul>
  </section>

  <section class="strengths">
    <p class="strengths-intro">We can help! Tap into our service for short or long term support. Our team is ready to jump in and make an impact on your business.</p>
    <span class="strength-rule" style="left:272px"></span>
    <span class="strength-rule" style="left:554px"></span>
    <div class="strength-grid">
      <div class="strength"><span class="strength-icon"><svg viewBox="0 0 26 26"><circle cx="7" cy="8" r="3" fill="#fff"/><circle cx="13" cy="6" r="3" fill="#fff"/><circle cx="19" cy="8" r="3" fill="#fff"/><path d="M4 22v-9h6v9zM10 20v-9h6v9zM16 22v-9h6v9z" fill="#fff"/></svg></span><span class="strength-label">Senior<br>Leadership</span></div>
      <div class="strength"><span class="strength-icon"><svg viewBox="0 0 26 26"><path d="M2 13c4-6 18-6 22 0-4 6-18 6-22 0z" fill="#fff"/><circle cx="13" cy="13" r="4" fill="#d41f63"/></svg></span><span class="strength-label">Modern<br>Perspective</span></div>
      <div class="strength"><span class="strength-icon"><svg viewBox="0 0 26 26"><circle cx="13" cy="14" r="3" fill="#fff"/><path d="M9 24v-6h8v6z" fill="#fff"/><path d="M5 4l2 3H3zM21 4l2 3h-4z" fill="#fff"/><rect x="11" y="2" width="4" height="4" fill="#fff"/></svg></span><span class="strength-label">Depth of<br>Perspective</span></div>
      <div class="strength"><span class="strength-icon"><svg viewBox="0 0 26 26"><circle cx="8" cy="6" r="2.5" fill="#fff"/><circle cx="18" cy="6" r="2.5" fill="#fff"/><path d="M5 22v-12h6v12zM15 22v-12h6v12z" fill="#fff"/><path d="M11 13h4" stroke="#fff" stroke-width="2"/></svg></span><span class="strength-label">Collaborative<br>Mindset</span></div>
      <div class="strength"><span class="strength-icon"><svg viewBox="0 0 26 26"><rect x="5" y="3" width="14" height="19" rx="1" fill="none" stroke="#fff" stroke-width="2"/><circle cx="14" cy="14" r="4" fill="none" stroke="#fff" stroke-width="2"/></svg></span><span class="strength-label">Practical<br>Tools</span></div>
      <div class="strength"><span class="strength-icon"><svg viewBox="0 0 26 26"><circle cx="13" cy="14" r="9" fill="none" stroke="#fff" stroke-width="2"/><circle cx="13" cy="14" r="4.5" fill="none" stroke="#fff" stroke-width="2"/><circle cx="13" cy="14" r="1.5" fill="#fff"/><path d="M13 14L5 4" stroke="#fff" stroke-width="2"/></svg></span><span class="strength-label">Goal<br>Oriented</span></div>
    </div>
  </section>

  <p class="team">The RPT team is composed of highly motivated experts who are delivering focused on flawless and impactful results for you!</p>

  <section class="contact-bar">
    <div class="contact-tab">Call me personally to discuss your challenge:</div>
    <div class="contact-name">
      <svg class="ico" viewBox="0 0 22 22"><circle cx="11" cy="11" r="9.5" fill="none" stroke="#fff" stroke-width="1.5"/><circle cx="11" cy="8" r="3" fill="#fff"/><path d="M5.5 17c1-4 10-4 11 0z" fill="#fff"/></svg>
      <span><b>CLAIRE HOLDEN</b><span class="title">, PRESIDENT</span></span>
      <svg class="ico" viewBox="0 0 22 22" style="margin-left:10px"><circle cx="11" cy="11" r="9.5" fill="none" stroke="#fff" stroke-width="1.5"/><rect x="8" y="5" width="6" height="12" rx="1" fill="none" stroke="#fff" stroke-width="1.5"/></svg>
      <span class="phone">(555) 014-2290</span>
    </div>
    <div class="contact-links">
      <svg class="ico" viewBox="0 0 22 22"><circle cx="11" cy="11" r="9.5" fill="none" stroke="#fff" stroke-width="1.3"/><rect x="6" y="7.5" width="10" height="7" fill="none" stroke="#fff" stroke-width="1.3"/><path d="M6 7.5l5 4 5-4" fill="none" stroke="#fff" stroke-width="1.3"/></svg>
      <span>claire@rptpartners.com</span>
      <span class="gap"></span>
      <svg class="ico" viewBox="0 0 22 22"><circle cx="11" cy="11" r="9.5" fill="none" stroke="#fff" stroke-width="1.3"/><circle cx="11" cy="11" r="5" fill="none" stroke="#fff" stroke-width="1.3"/><path d="M6 11h10M11 6v10" stroke="#fff" stroke-width="1.1"/></svg>
      <span>rptpartners.com</span>
    </div>
  </section>

  <div class="portrait" role="img" aria-label="Portrait photo of the company president"></div>
</main>
</body>
</html>
```